Eyecatching website design for commercial lighting business

This contest is all about the graphic design aspect. We need a striking website design for a commercial lighting company. We want something really eye catching to introduce people to our range of induction and LED lights which save businesses money on maintenance and electricity costs.

To be successful in this contest you will need to provide a design and pictures for the pages listed below.

We are using the platform velbrin.com.au and you can see the attached template which everything will be loaded into so we just need HTML files which we can upload and we can do everything else from Velbrin.

The final design should be strong and clean and use the colours and textures in the attached business card file.

Detailed requirements:

Please see attached screenshot of the website template, all we need is a fantastic graphic design and improvement/ incorporation of our logo for the following pages
Page Headings:
1. Home
About Us, Contact Us, snapshot of and link to Blog

Each of the below pages will have several paragraphs of text followed by a list of suitable products which is generated from our product catalogue.

2. Car Park Lighting
3. Educational Lighting
4. Hospitality Lighting
5. Office & Shop Lighting
6. Warehouse Lighting

Some of the website we have seen which are similar in nature are:
http://www.quorvanlamps.com.au/
http://www.tibrox.com/
http://www.gandowlumen.net/commercial-led
but we really want a modern, eye catching and memorable design

Some of the designs built on Velbrin that we like are:

http://www.pemberhollow.com.au/
http://www.marwickgoods.com.au/
http://www.kelmorabay.com.au/

I've also uploaded a couple of photos that we love. We'd like something similar for each industry.

Target Market(s)

Company Owners, Maintenance & Facilities Managers, Electrical Contractors

Industry/Entity Type

Electrical

Coding

Coded - Design and coding required

Number of Pages Required

5+ page

Font styles to use
Sans Serif

Colors
33a6d7
ec1f27

Requirements
Must have
• -Must scale to mobile
• -HTML coded files need to be provided (HTML Bootstrap)
Nice to have
• -Prefer incorporation of our logo into header bar
• -Design of 2-3 advertising banners which can be displayed on the home page
• -Prominent call to action button towards top of page 'Get a quote' or similar
• -Grid based design HTML Bootstrap

```html
<!DOCTYPE html>
<html lang="en">
<head>
<meta charset="utf-8">
<title>Lumvale Business Solutions — Commercial &amp; Industrial Lighting</title>
<link href="https://fonts.googleapis.com/css2?family=Open+Sans:wght@300;400;600;700&display=swap" rel="stylesheet">
<style>
:root{
  --blue:#33a6d7;
  --red:#ec1f27;
  --ink:#222222;
  --text:#555555;
  --muted:#8a8a8a;
  --header:#0f0f10;
  --band:#ededed;
  --white:#ffffff;
  --dark:#121417;
}
*{margin:0;padding:0;box-sizing:border-box}
html,body{width:1200px;height:2212px;overflow:hidden}
body{font-family:"Open Sans",Arial,sans-serif;color:var(--text);background:var(--white);position:relative}

.site-header{height:110px;background:var(--header);display:flex;align-items:center;justify-content:space-between;padding:0 96px 0 60px}
.brand{display:flex;align-items:center;gap:14px}
.brand-mark{width:34px;height:34px;border-radius:50%;background:var(--red)}
.brand-name{color:var(--red);font-weight:700;font-size:22px;letter-spacing:1px;text-transform:uppercase}
.main-nav{display:flex;gap:6px}
.main-nav a{color:var(--white);text-decoration:none;font-size:13px;font-weight:600;letter-spacing:.5px;padding:10px 16px}
.main-nav a.active{background:var(--blue)}

.hero{position:relative;height:505px;background:linear-gradient(180deg,#c9c6c0 0%,#b9b3aa 40%,#8f8a82 70%,#6e6a64 100%)}
.hero-caption{position:absolute;right:100px;top:270px;text-align:right;color:var(--white)}
.hero-caption .kicker{font-size:26px;font-weight:300;letter-spacing:1px;color:#f2d7a4}
.hero-caption h1{font-size:46px;font-weight:700;letter-spacing:1px;line-height:1.2}
.hero-dots{position:absolute;left:0;right:0;bottom:30px;display:flex;justify-content:center;gap:8px}
.hero-dots span{width:10px;height:10px;border-radius:50%;background:rgba(255,255,255,.6)}
.hero-dots span.on{background:var(--white)}

.btn{display:inline-block;background:var(--blue);color:var(--white);font-size:12px;font-weight:600;letter-spacing:.5px;text-transform:uppercase;padding:11px 26px;text-decoration:none}
.btn.small{padding:8px 18px;font-size:11px}

.welcome{height:285px;text-align:center;padding:50px 150px 0}
.section-title{font-size:28px;font-weight:600;color:var(--ink);letter-spacing:.5px;text-transform:uppercase}
.welcome p{font-size:13px;line-height:1.7;margin:22px 0 28px}

.solutions{height:480px;background:var(--band);padding:40px 88px 0}
.solutions-head{display:flex;align-items:center;justify-content:center;gap:24px}
.arrow{width:26px;height:26px;background:var(--red);display:flex;align-items:center;justify-content:center}
.solution-grid{display:grid;grid-template-columns:repeat(3,1fr);gap:40px;margin-top:40px}
.solution-photo{height:160px}
.photo-carpark{background:linear-gradient(180deg,#5c6c7a,#2d3944)}
.photo-edu{background:linear-gradient(180deg,#c8d3dc,#7f8c97)}
.photo-hosp{background:linear-gradient(180deg,#d8d2c6,#8c8175)}
.solution-card h3{font-size:17px;font-weight:600;color:var(--ink);margin:26px 0 8px}
.solution-card p{font-size:12px;line-height:1.6;margin-bottom:18px}

.video{height:360px;background:linear-gradient(90deg,#0c0e10,#1c2126 60%,#0d1013);position:relative;padding:50px 0 0 88px}
.video-intro{width:420px;color:#d8d8d8}
.video-intro h2{color:var(--white);font-size:28px;font-weight:600;text-transform:uppercase;text-align:center;margin-bottom:16px}
.video-intro p{font-size:12.5px;line-height:1.6;margin-bottom:22px}
.video-intro .btn{margin-left:140px}
.video-player{position:absolute;left:592px;top:60px;width:508px;height:280px;border:2px solid #2f3a42}
.video-frame{position:absolute;inset:0 0 34px 0;background:radial-gradient(ellipse at 55% 40%,#9ab0bd 0%,#2c3f4c 35%,#0b1116 75%)}
.video-controls{position:absolute;left:0;right:0;bottom:0;height:34px;background:#1a1d20;display:flex;align-items:center;gap:12px;padding:0 12px;color:#cfcfcf;font-size:11px}
.progress{flex:1;height:4px;background:#444;position:relative}
.progress span{position:absolute;left:0;top:0;height:4px;width:45%;background:var(--blue)}

.blog{height:420px;background:linear-gradient(180deg,#f4f4f4,#e6e6e6);padding:110px 88px 0;text-align:center}
.blog-grid{display:grid;grid-template-columns:repeat(3,1fr);gap:60px;margin-top:36px;text-align:left}
.blog-post h4{font-size:14px;font-weight:700;color:var(--ink);text-transform:uppercase}
.blog-post time{display:block;font-size:11px;color:var(--muted);margin:6px 0 10px}
.blog-post p{font-size:12px;line-height:1.6;margin-bottom:10px}
.blog-post a{font-size:11px;color:var(--red);text-decoration:none;font-weight:600}

.site-footer{position:absolute;left:0;bottom:0;width:1200px;height:52px;background:var(--red);display:flex;align-items:center;justify-content:space-between;padding:0 88px;color:var(--white);font-size:11px}
.social{display:flex;gap:6px}
.social span{width:22px;height:22px;background:var(--blue)}
</style>
</head>
<body>

<header class="site-header">
  <div class="brand">
    <span class="brand-mark"></span>
    <span class="brand-name">Lumvale Business Solutions</span>
  </div>
  <nav class="main-nav">
    <a href="#" class="active">HOME</a>
    <a href="#">ABOUT US</a>
    <a href="#">PRODUCTS</a>
    <a href="#">BLOG</a>
    <a href="#">CONTACT US</a>
  </nav>
</header>

<section class="hero" role="img" aria-label="Bright modern interior with a recessed circular ceiling light feature">
  <div class="hero-caption">
    <div class="kicker">THE BEST RANGE OF ENERGY SAVING</div>
    <h1>COMMERCIAL &amp; INDUSTRIAL LIGHTING</h1>
  </div>
  <div class="hero-dots"><span class="on"></span><span></span><span></span><span></span></div>
</section>

<section class="welcome">
  <h2 class="section-title">Welcome to Lumvale Business Solutions</h2>
  <p>Retrofitting the lighting in a commercial or industrial premises is a great way to save money on energy costs and maintenance, create a safer work environment and reduce the load on the wiring in the premises. When you are considering a retrofit of a commercial building there are a number of technologies on the market and a lot to consider.</p>
  <a href="#" class="btn">Read More</a>
</section>

<section class="solutions">
  <div class="solutions-head">
    <span class="arrow"><svg width="10" height="12" viewBox="0 0 10 12"><path d="M8 1 2 6l6 5" fill="none" stroke="#fff" stroke-width="2"/></svg></span>
    <h2 class="section-title">Our Solutions</h2>
    <span class="arrow"><svg width="10" height="12" viewBox="0 0 10 12"><path d="M2 1l6 5-6 5" fill="none" stroke="#fff" stroke-width="2"/></svg></span>
  </div>
  <div class="solution-grid">
    <article class="solution-card">
      <div class="solution-photo photo-carpark" role="img" aria-label="Underground car park lit by LED fittings"></div>
      <h3>Car Park Lighting</h3>
      <p>LED car park lights cut running costs, improve visibility and keep drivers and pedestrians safe around the clock.</p>
      <a href="#" class="btn small">Read More</a>
    </article>
    <article class="solution-card">
      <div class="solution-photo photo-edu" role="img" aria-label="Bright classroom with rows of desks under ceiling lights"></div>
      <h3>Educational Lighting</h3>
      <p>Bright, even lighting for classrooms and halls that helps students focus while lowering energy bills for schools.</p>
      <a href="#" class="btn small">Read More</a>
    </article>
    <article class="solution-card">
      <div class="solution-photo photo-hosp" role="img" aria-label="Hotel lounge with warm pendant lighting"></div>
      <h3>Hospitality Lighting</h3>
      <p>Warm, efficient lighting for hotels, bars and restaurants that sets the mood and lasts for years.</p>
      <a href="#" class="btn small">Read More</a>
    </article>
  </div>
</section>

<section class="video" role="region" aria-label="Latest video">
  <div class="video-intro">
    <h2>Our Latest Video</h2>
    <p>See how our induction and LED fittings transform a warehouse floor. Our team walks through the retrofit process from first site audit to final installation, showing the savings on power and maintenance that businesses can expect in the first year.</p>
    <a href="#" class="btn">Read More</a>
  </div>
  <div class="video-player">
    <div class="video-frame" role="img" aria-label="Video still of bright floodlights at night"></div>
    <div class="video-controls">
      <svg width="12" height="14" viewBox="0 0 12 14"><path d="M1 1l10 6-10 6z" fill="#fff"/></svg>
      <span>00:00</span>
      <div class="progress"><span></span></div>
      <span>03:12</span>
      <svg width="16" height="14" viewBox="0 0 16 14"><path d="M1 5h3l4-3v10L4 9H1z" fill="#fff"/><path d="M11 4c1.5 1.5 1.5 4.5 0 6" stroke="#fff" fill="none" stroke-width="1.5"/></svg>
    </div>
  </div>
</section>

<section class="blog">
  <h2 class="section-title">Latest Blog</h2>
  <div class="blog-grid">
    <article class="blog-post">
      <h4>Government Sectors</h4>
      <time>Jun 28 2015</time>
      <p>The rebates on offer to the government sector make a switch to LED lighting easier than ever before.</p>
      <a href="#">Read More »</a>
    </article>
    <article class="blog-post">
      <h4>Government Sectors</h4>
      <time>Jun 28 2015</time>
      <p>The rebates on offer to the government sector make a switch to LED lighting easier than ever before.</p>
      <a href="#">Read More »</a>
    </article>
    <article class="blog-post">
      <h4>Government Sectors</h4>
      <time>Jun 28 2015</time>
      <p>The rebates on offer to the government sector make a switch to LED lighting easier than ever before.</p>
      <a href="#">Read More »</a>
    </article>
  </div>
</section>

<footer class="site-footer">
  <span>Copyright © 2015 Lumvale Business Solutions Inc. All rights reserved.</span>
  <div class="social" aria-label="Social links"><span></span><span></span><span></span></div>
</footer>

</body>
</html>
```